Logistics Website Design

See website https://tqfreightglobal.com for theme and color details. Need the site to be re-done and reflect some of the designs shown in this list here: https://pixelvane.com/tags/logistics-company-website

Target Market(s)

Logistics & Transportation

Industry/Entity Type

Logistics and Supply Chain

Coding

Number of Pages Required

5+ page

Requirements
Must have
• Colors must match theme of logo. Looking for a sleek, interactive design.

```html
<!DOCTYPE html>
<html lang="en">
<head>
<meta charset="utf-8">
<title>TQ Freight Global — Logistics</title>
<link href="https://fonts.googleapis.com/css2?family=Inter:wght@400;500;700&family=Playfair+Display:wght@400;700&family=Libre+Baskerville:wght@700&display=swap" rel="stylesheet">
<style>
:root{
  --accent:#d98a6c;
  --accent-dark:#c9714f;
  --ink:#1f2937;
  --heading:#414b5a;
  --body:#4b5563;
  --muted:#5f6672;
  --panel:#f6f7f9;
  --rule:#e2e4e8;
  --white:#ffffff;
}
*{box-sizing:border-box;margin:0;padding:0}
html,body{width:1200px;height:2477px;overflow:hidden;background:var(--white)}
body{font-family:"Inter",sans-serif;color:var(--ink);position:relative}

.site-header{position:absolute;top:0;left:0;width:1200px;height:75px;background:var(--white);z-index:3}
.brand{position:absolute;left:32px;top:6px;display:flex;align-items:center;gap:10px}
.brand-mark{width:62px;height:62px;border-radius:50%;background:var(--accent)}
.brand-name{font-family:"Inter",sans-serif;font-weight:700;font-size:16px;color:var(--ink);letter-spacing:.02em}
.main-nav{position:absolute;top:28px;left:362px;display:flex;gap:30px;font-size:13.5px;color:var(--ink)}
.main-nav a{text-decoration:none;color:inherit;padding-bottom:6px}
.main-nav a.is-active{color:var(--accent-dark);border-bottom:2px solid var(--accent)}
.btn{display:inline-flex;align-items:center;justify-content:center;background:var(--accent);color:var(--white);text-decoration:none;font-weight:500;border-radius:3px}
.header-cta{position:absolute;right:32px;top:19px;width:163px;height:37px;font-size:15px}

.hero{position:absolute;top:75px;left:0;width:1200px;height:713px;background:radial-gradient(ellipse at 75% 50%,#4a4238 0%,#262623 35%,#0d0e0d 75%)}
.hero-photo{position:absolute;inset:0}
.hero-copy{position:absolute;left:32px;top:187px;width:460px;color:var(--white)}
.hero-title{font-family:"Playfair Display",serif;font-weight:400;font-size:67px;line-height:67px;letter-spacing:-.005em}
.hero-sub{margin-top:20px;font-size:19.5px;line-height:26px}
.hero-cta{margin-top:34px;width:192px;height:48px;font-size:17px}

.intro{position:absolute;top:788px;left:0;width:1200px;height:770px;background:var(--panel)}
.intro-photo{position:absolute;left:32px;top:75px;width:545px;height:546px;background:linear-gradient(180deg,#8a7a8f 0%,#e9a85c 22%,#8d7c66 45%,#5d554b 100%);box-shadow:0 4px 10px rgba(0,0,0,.15)}
.intro-rule{position:absolute;left:623px;top:58px;width:2px;height:579px;background:var(--accent)}
.intro-copy{position:absolute;left:654px;top:114px;width:520px}
.intro-title{font-weight:700;font-size:35px;line-height:44px;color:var(--heading)}
.intro-text{margin-top:12px;font-size:23px;line-height:37.4px;color:var(--body)}
.intro-divider{position:absolute;left:32px;top:696px;width:1136px;height:1px;background:var(--rule)}

.services{position:absolute;top:1558px;left:0;width:1200px}
.services-title{position:absolute;top:76px;width:1200px;text-align:center;font-family:"Playfair Display",serif;font-weight:400;font-size:36px;letter-spacing:.06em;color:var(--ink)}
.service-list{position:absolute;top:173px;left:32px;display:flex;gap:30px}
.service-card{width:262px;text-align:center}
.service-photo{height:180px}
.service-name{margin-top:28px;font-family:"Libre Baskerville",serif;font-weight:700;font-size:16px;line-height:26px;color:#2d2d2d}
.service-bar{width:46px;height:3px;background:var(--accent);opacity:.7;margin:10px auto 12px}
.service-text{font-size:13.5px;line-height:19px;color:var(--muted);padding:0 4px}
.services-divider{position:absolute;top:570px;left:32px;width:1136px;height:1px;background:var(--rule)}

.site-footer{position:absolute;top:2210px;left:0;width:1200px;text-align:center}
.footer-brand{display:flex;flex-direction:column;align-items:center;gap:10px}
.footer-brand .brand-mark{width:92px;height:92px}
.footer-brand .brand-name{font-size:18px}
.copyright{position:absolute;top:156px;width:1200px;font-size:13.5px;color:var(--muted)}
.social{position:absolute;top:200px;left:0;width:1200px;display:flex;justify-content:center;gap:22px}
.social-dot{width:16px;height:16px;border-radius:50%;background:#3a3f47}
.social svg{width:18px;height:18px}
</style>
</head>
<body>
<header class="site-header">
  <div class="brand"><span class="brand-mark"></span><span class="brand-name">TQ FREIGHT GLOBAL</span></div>
  <nav class="main-nav">
    <a class="is-active" href="#">Home</a>
    <a href="#">Services</a>
    <a href="#">Industries</a>
    <a href="#">Request a Quote</a>
    <a href="#">Contact Us</a>
  </nav>
  <a class="btn header-cta" href="#">Request a Quote</a>
</header>

<section class="hero">
  <div class="hero-photo" role="img" aria-label="Semi truck with headlights on driving through heavy rain at night"></div>
  <div class="hero-copy">
    <h1 class="hero-title">DELIVERING STRENGTH IN EVERY MILE</h1>
    <p class="hero-sub">Secure and reliable transportation for all your cargo needs.</p>
    <a class="btn hero-cta" href="#">Request a Quote</a>
  </div>
</section>

<section class="intro">
  <div class="intro-photo" role="img" aria-label="Aerial view of a truck yard at sunset with flatbed trucks, a tanker and heavy equipment"></div>
  <div class="intro-rule"></div>
  <div class="intro-copy">
    <h2 class="intro-title">Keeping Your Supply Chain Moving</h2>
    <p class="intro-text">We deliver a comprehensive range of open-deck and specialized transportation services, including flatbed, step deck, heavy haul, and over-dimensional freight solutions. Backed by years of experience, a trusted nationwide carrier network, and a strong safety-first culture, we provide reliable, adaptable logistics support built around the unique requirements of every load.</p>
  </div>
  <div class="intro-divider"></div>
</section>

<section class="services">
  <h2 class="services-title">OUR SERVICES</h2>
  <div class="service-list">
    <article class="service-card">
      <div class="service-photo" role="img" aria-label="Flatbed truck carrying a wrapped wind turbine blade on a coastal highway" style="background:linear-gradient(180deg,#c9d3d6 0%,#a79670 50%,#4a4a48 100%)"></div>
      <h3 class="service-name">FLATBED<br>TRANSPORTATION</h3>
      <div class="service-bar"></div>
      <p class="service-text">From routine shipments to oversized and heavy-haul loads, we handle freight requiring proper securement, regulatory knowledge, and consistent on-time execution.</p>
    </article>
    <article class="service-card">
      <div class="service-photo" role="img" aria-label="Step deck trailer hauling an industrial transformer at dusk" style="background:linear-gradient(180deg,#3f6ea8 0%,#7c6a5c 55%,#3b3733 100%)"></div>
      <h3 class="service-name">STEP DECK<br>TRANSPORTATION</h3>
      <div class="service-bar"></div>
      <p class="service-text">Our step deck trucking services support tall, heavy, and specialized freight that requires additional height clearance and flexible loading options.</p>
    </article>
    <article class="service-card">
      <div class="service-photo" role="img" aria-label="Three white dry van trucks leaving a logistics warehouse" style="background:linear-gradient(180deg,#c7d4e0 0%,#8b939a 50%,#6b6f73 100%)"></div>
      <h3 class="service-name">DRY VAN<br>TRANSPORTATION</h3>
      <div class="service-bar"></div>
      <p class="service-text">From consumer goods to industrial materials, our dry van services provide the space, security, and consistency you need coast to coast.</p>
    </article>
    <article class="service-card">
      <div class="service-photo" role="img" aria-label="Heavy haul trailer moving a large industrial vessel at an industrial site" style="background:linear-gradient(180deg,#e6b87a 0%,#8a6a4e 50%,#3a2f2a 100%)"></div>
      <h3 class="service-name">HEAVY HAUL<br>TRANSPORTATION</h3>
      <div class="service-bar"></div>
      <p class="service-text">We provide heavy haul trucking solutions for oversized, overweight, and over-dimensional freight.</p>
    </article>
  </div>
  <div class="services-divider"></div>
</section>

<footer class="site-footer">
  <div class="footer-brand"><span class="brand-mark"></span><span class="brand-name">TQ FREIGHT GLOBAL</span></div>
  <p class="copyright">© 2024. An independent agent of Harlow Brandt LLC.</p>
  <div class="social">
    <span class="social-dot"></span>
    <span class="social-dot"></span>
    <span class="social-dot"></span>
    <svg viewBox="0 0 24 24" aria-label="Phone"><path fill="#3a3f47" d="M6.6 10.8a15 15 0 0 0 6.6 6.6l2.2-2.2a1 1 0 0 1 1-.25 11.4 11.4 0 0 0 3.6.6 1 1 0 0 1 1 1V20a1 1 0 0 1-1 1A17 17 0 0 1 3 4a1 1 0 0 1 1-1h3.5a1 1 0 0 1 1 1c0 1.25.2 2.45.6 3.6a1 1 0 0 1-.25 1z"/></svg>
  </div>
</footer>
</body>
</html>
```